Boutique town planning business needs a Business Card design

We need a business card design for a new company called The Zoning Bridgeway. We provide town planning and urban design services to government, business and community groups. We would like to see the designs use the colours in the logo (blue, deep red, green and amber), plenty of white and including black and grey in the writing. The final design should communicate collaboration, creativity and professionalism and that we are approachable.

Industry/Entity Type

Town

```html
<!DOCTYPE html>
<html lang="en">
<head>
<meta charset="utf-8">
<title>The Zoning Bridgeway – Business Card</title>
<link rel="stylesheet" href="https://fonts.googleapis.com/css2?family=Ubuntu:wght@400;500;700&display=swap">
<style>
  :root {
    --stage: #e6e7e9;
    --card: #ffffff;
    --ink: #2b2b2b;
    --grey: #6d7073;
    --grey-light: #b9bcbf;
    --faint: #f1f2f3;
    --black: #1f1c1b;
    --deep-red: #a3262a;
    --amber: #e37c1f;
    --blue: #1a8fd3;
  }
  * { box-sizing: border-box; margin: 0; padding: 0; }
  html, body { width: 1200px; height: 912px; overflow: hidden; }
  body {
    background: var(--stage);
    font-family: "Ubuntu", sans-serif;
    position: relative;
  }
  .card {
    position: absolute;
    width: 620px;
    height: 360px;
    background: var(--card);
    overflow: hidden;
    box-shadow: 0 6px 18px rgba(0,0,0,0.18);
  }
  .card--front { left: 60px; top: 70px; }
  .card--back { left: 520px; top: 480px; }

  .faint-ring {
    position: absolute;
    border-radius: 50%;
    border: 26px solid var(--faint);
  }
  .card--front .faint-ring { width: 330px; height: 330px; right: -40px; top: 10px; }
  .card--back .faint-ring { width: 300px; height: 300px; right: -60px; top: 20px; }

  .brand {
    position: absolute;
    display: flex;
    align-items: center;
    gap: 14px;
    z-index: 1;
  }
  .brand__dot {
    flex: none;
    border-radius: 50%;
    background: var(--blue);
  }
  .brand__name {
    font-weight: 700;
    color: var(--ink);
    line-height: 1;
    white-space: nowrap;
  }
  .card--front .brand { left: 150px; top: 150px; }
  .card--front .brand__dot { width: 46px; height: 46px; }
  .card--front .brand__name { font-size: 34px; }

  .card--back .brand { left: 44px; top: 44px; }
  .card--back .brand__dot { width: 34px; height: 34px; }
  .card--back .brand__name { font-size: 25px; }

  .contact {
    position: absolute;
    left: 44px;
    top: 134px;
    list-style: none;
    z-index: 1;
  }
  .contact__item {
    display: flex;
    align-items: center;
    gap: 12px;
    font-size: 15px;
    color: var(--ink);
    height: 29px;
  }
  .contact__icon { width: 16px; height: 16px; flex: none; fill: var(--deep-red); }

  .wave { position: absolute; left: 0; top: 0; width: 620px; height: 360px; }

  .holder {
    position: absolute;
    right: 34px;
    bottom: 20px;
    text-align: right;
    z-index: 1;
  }
  .holder__name {
    font-weight: 700;
    font-size: 19px;
    line-height: 1.2;
    color: var(--amber);
    margin-bottom: 4px;
  }
  .holder__detail {
    font-size: 11px;
    line-height: 1.45;
    color: #ffffff;
  }
</style>
</head>
<body>

  <section class="card card--front" aria-label="Business card front">
    <div class="faint-ring"></div>
    <div class="brand">
      <span class="brand__dot"></span>
      <span class="brand__name">The Zoning Bridgeway</span>
    </div>
  </section>

  <section class="card card--back" aria-label="Business card back">
    <div class="faint-ring"></div>
    <div class="brand">
      <span class="brand__dot"></span>
      <span class="brand__name">The Zoning Bridgeway</span>
    </div>

    <ul class="contact">
      <li class="contact__item">
        <svg class="contact__icon" viewBox="0 0 16 16"><path d="M2 5c0-2 2-3 6-3s6 1 6 3v1h-3V5H5v1H2z M3 8h10l1 6H2z M6 9h4v2H6z"/></svg>
        0412 358 907
      </li>
      <li class="contact__item">
        <svg class="contact__icon" viewBox="0 0 16 16"><path d="M1 3h14v10H1z M2 4.2v.6l6 4 6-4v-.6z" fill-rule="evenodd"/></svg>
        thezoningbridgeway@mailhub.com
      </li>
      <li class="contact__item">
        <svg class="contact__icon" viewBox="0 0 16 16"><circle cx="8" cy="8" r="7"/><path d="M1 8h14M8 1c-3 3-3 11 0 14M8 1c3 3 3 11 0 14" stroke="#fff" stroke-width="1.1" fill="none"/></svg>
        www.thezoningbridgeway.com.au
      </li>
      <li class="contact__item">
        <svg class="contact__icon" viewBox="0 0 16 16"><path d="M5 1h2l-.6 4h3L10 1h2l-.6 4H14v2h-2.9l-.4 2H14v2h-3.6L10 15H8l.4-4h-3L5 15H3l.4-4H1V9h2.7l.4-2H1V5h3.4zM6.1 7l-.4 2h3l.4-2z"/></svg>
        ABN 51203884617
      </li>
    </ul>

    <svg class="wave" viewBox="0 0 620 360" aria-hidden="true">
      <path d="M0 238 C130 288 250 298 360 248 S520 166 620 156 L620 176 C560 180 470 214 360 266 C250 316 120 304 0 256Z" fill="var(--grey)"/>
      <path d="M0 262 C130 312 250 322 360 272 S520 190 620 180 L620 186 C560 190 470 222 360 278 C250 328 120 318 0 268Z" fill="var(--grey-light)"/>
      <path d="M0 276 C130 324 250 332 360 282 S520 200 620 192 L620 360 L0 360Z" fill="var(--black)"/>
    </svg>

    <div class="holder">
      <p class="holder__name">Marguerite Ellison</p>
      <p class="holder__detail">BTD (Civic Design),<br>GDipSP, MCPG, RZPA<br>Principal</p>
    </div>
  </section>

</body>
</html>
```